A resume/portfolio website for myself

I'm an independent software contractor, architect, tech trainer. I need a web site to present myself. Many ready to use portfolio designs are too artistic and focused on presenting design skills of the person. I like a nice website but the content should be a little less graphic than if you would present a graphic designer. Content could be presentation of me, core skill qualities and services and resume. Potentially a page with my tech courses in the longer run

```html
<!DOCTYPE html>
<html lang="en">
<head>
<meta charset="utf-8">
<title>Daniel Hartvig — Software Contractor</title>
<link href="https://fonts.googleapis.com/css2?family=Montserrat:wght@400;500;600&family=Roboto:wght@400;500&display=swap" rel="stylesheet">
<style>
:root{
  --navy:#0a2b9c;
  --blue:#2746c6;
  --blue-mid:#2a47c2;
  --blue-light:#3f63dc;
  --btn:#4a72e6;
  --ink:#222;
  --text:#333;
  --muted:#555;
  --grey-bg:#f4f4f4;
  --edu-bg:#f1f1f1;
  --photo:#8a8a8a;
}
*{margin:0;padding:0;box-sizing:border-box}
html,body{width:1200px;height:3850px;overflow:hidden;background:#fff}
body{position:relative;font-family:'Roboto',sans-serif;color:var(--text)}
.abs{position:absolute}
.mont{font-family:'Montserrat',sans-serif}

.nav{top:0;left:0;width:1200px;height:78px;background:#fff;display:flex;justify-content:center;align-items:center;gap:32px;font-family:'Montserrat',sans-serif;font-size:17px;color:var(--ink)}
.nav .active{color:var(--blue)}

.hero-top{top:78px;left:0;width:1200px;height:133px;background:var(--blue)}
.hero-main{top:211px;left:0;width:1200px;height:446px;background:var(--navy)}
.hero-strip{top:657px;left:0;width:1200px;height:66px;background:var(--blue);display:flex;justify-content:center;align-items:center;gap:52px;color:#fff;font-size:17px}
.hero-strip span{display:flex;align-items:center;gap:14px}
.social{top:112px;left:90px;display:flex;gap:20px;align-items:center}
.social .sq{width:22px;height:22px;border-radius:3px;background:#fff}
.btn-resume{top:97px;left:835px;width:275px;height:57px;background:#3f66e0;border:1px solid #6a8af0;border-radius:4px;color:#fff;font-family:'Montserrat',sans-serif;font-size:18px;display:flex;align-items:center;justify-content:center;box-shadow:0 3px 6px rgba(0,0,0,.2)}
.hero-name{top:180px;left:0;width:1200px;text-align:center;color:#fff;font-family:'Montserrat',sans-serif;font-size:57px;font-weight:500;letter-spacing:1px}
.hero-sub{top:268px;left:0;width:1200px;text-align:center;color:#fff;font-family:'Montserrat',sans-serif;font-size:29px}
.hero-roles{top:329px;left:0;width:1200px;text-align:center;color:#fff;font-size:16px;font-weight:500;word-spacing:1px}
.hero-text{top:396px;left:170px;width:860px;text-align:center;color:#fff;font-size:18px;line-height:37px}

.about-h{top:808px;left:90px;color:var(--navy);font-family:'Montserrat',sans-serif;font-size:38px;line-height:44px;font-weight:500}
.about-p{top:928px;left:90px;width:540px;font-size:18.5px;line-height:37.5px;text-align:justify;color:var(--text)}
.btn-more{top:1181px;left:90px;width:240px;height:71px;background:var(--btn);border-radius:4px;color:#fff;font-family:'Montserrat',sans-serif;font-size:21px;display:flex;align-items:center;justify-content:center}
.about-photo{top:820px;left:707px;width:403px;height:432px;background:linear-gradient(160deg,#b5b5b5,#7a7a7a 60%,#3a3a3a)}

.work-bg{top:1352px;left:0;width:1200px;height:894px;background:var(--grey-bg)}
.work-card{top:1417px;left:109px;width:982px;height:780px;background:#fff;box-shadow:2px 2px 5px rgba(0,0,0,.2)}
.sec-title{left:0;width:1200px;text-align:center;color:var(--blue);font-family:'Montserrat',sans-serif;font-size:35px;font-weight:500}
.role{left:127px;font-family:'Montserrat',sans-serif;font-size:17px;color:var(--navy);line-height:24px}
.role b{display:block;font-weight:500;color:var(--ink)}
.company{left:450px;font-family:'Montserrat',sans-serif;font-size:18px;color:var(--ink)}
.desc{left:450px;width:380px;font-size:16px;line-height:31px;color:var(--muted)}
.place{left:900px;font-family:'Montserrat',sans-serif;font-size:15px;color:var(--navy);display:flex;align-items:center;gap:14px}

.edu-box{top:2436px;left:90px;width:1020px;height:344px;background:var(--edu-bg);box-shadow:2px 2px 5px rgba(0,0,0,.25)}
.edu-t{font-family:'Montserrat',sans-serif;font-size:18px;color:var(--blue)}
.edu-s{font-family:'Montserrat',sans-serif;font-size:16px;color:var(--ink);line-height:29px}

.skill-ring{top:3027px;width:186px;height:186px}
.skill-label{top:3238px;width:360px;text-align:center;font-family:'Montserrat',sans-serif;font-size:18px;color:var(--ink)}
.skill-desc{top:3278px;width:300px;text-align:center;font-size:13px;line-height:23px;color:var(--muted)}

.touch{top:3446px;left:0;width:1200px;height:342px;background:var(--blue-mid)}
.touch-h{top:3484px;left:0;width:1200px;text-align:center;color:#fff;font-family:'Montserrat',sans-serif;font-size:32px}
.touch-photo{top:3568px;left:89px;width:160px;height:160px;border-radius:50%;background:radial-gradient(circle at 50% 40%,#c9a48c,#6b5446 70%,#3d4a3a)}
.touch-p{top:3542px;left:296px;width:796px;color:#fff;font-size:18px;line-height:35px}
.touch-mail{top:3727px;left:296px;color:#fff;font-size:18px}
.footer{top:3788px;left:0;width:1200px;height:62px;background:var(--blue-light)}
.footer-copy{top:3805px;left:90px;color:#fff;font-family:'Montserrat',sans-serif;font-size:20px}
.footer-social{top:3808px;left:907px;display:flex;gap:20px;align-items:center}
.footer-social .sq{width:24px;height:24px;border-radius:3px;background:#fff}
</style>
</head>
<body>

<nav class="abs nav">
  <span class="active">HOME</span><span>ABOUT US</span><span>EXPERIENCE</span><span>EDUCATION</span><span>SKILLS</span><span>PORTFOLIO</span><span>CONTACT US</span>
</nav>

<header>
  <div class="abs hero-top"></div>
  <div class="abs hero-main"></div>
  <div class="abs social" aria-label="Social links">
    <span class="sq"></span><span class="sq"></span><span class="sq"></span><span class="sq"></span>
    <svg width="28" height="22" viewBox="0 0 28 22"><rect x="1.5" y="1.5" width="25" height="19" rx="2" fill="none" stroke="#fff" stroke-width="2.5"/><path d="M2 3l12 9 12-9" fill="none" stroke="#fff" stroke-width="2.5"/></svg>
  </div>
  <div class="abs btn-resume">DOWNLOAD MY RESUME</div>
  <h1 class="abs hero-name">DANIEL HARTVIG</h1>
  <div class="abs hero-sub">DANIEL HARTVIG</div>
  <div class="abs hero-roles">INDEPENDENT SOFTWARE CONTRACTOR &nbsp; / &nbsp; ARCHITECT &nbsp; / &nbsp; TECH TRAINER</div>
  <p class="abs hero-text">Sed ut perspiciatis unde omnis iste natus error sit voluptatem accusantium doloremque laudantium, totam rem aperiam, eaque ipsa quae ab illo inventore veritatis et quasi architecto beatae vitae dicta sunt explicabo. Nemo enim ipsam voluptatem quia voluptas sit aspernatur aut odit aut fugit, sed quia consequuntur magni dolores eos qui ratione voluptatem sequi nesciunt. Neque porro quisquam est, qui dolorem ipsum quia dolor sit amet, consectetur, adipisci velit, sed quia non numquam eius modi tempora incidunt ut labore et dolore magnam aliquam quaerat voluptatem.</p>
  <div class="abs hero-strip">
    <span><svg width="18" height="14" viewBox="0 0 18 14"><rect x="1" y="1" width="16" height="12" rx="1.5" fill="none" stroke="#fff" stroke-width="1.8"/><path d="M1.5 2l7.5 6 7.5-6" fill="none" stroke="#fff" stroke-width="1.8"/></svg>info@danielhartvig.com</span>
    <span><svg width="16" height="16" viewBox="0 0 24 24"><path fill="#fff" d="M6.6 10.8a15 15 0 006.6 6.6l2.2-2.2c.3-.3.7-.4 1-.2 1.1.4 2.3.6 3.6.6.6 0 1 .4 1 1V20c0 .6-.4 1-1 1A17 17 0 013 4c0-.6.4-1 1-1h3.5c.6 0 1 .4 1 1 0 1.3.2 2.5.6 3.6.1.3 0 .7-.2 1z"/></svg><span style="margin-left:22px">8888 888 8888</span></span>
  </div>
</header>

<section>
  <h2 class="abs about-h">ABOUT DANIEL<br>HARTVIG</h2>
  <p class="abs about-p">Sed ut perspiciatis unde omnis iste natus error sit voluptatem accusantium doloremque laudantium, totam rem aperiam, eaque ipsa quae ab illo inventore veritatis et quasi architecto beatae vitae dicta sunt explicabo. Nemo enim ipsam voluptatem quia voluptas sit aspernatur aut odit aut fugit, sed quia consequuntur magni dolores eos qui ratione</p>
  <div class="abs btn-more">READ MORE</div>
  <div class="abs about-photo" role="img" aria-label="Black and white portrait photo of Daniel Hartvig"></div>
</section>

<section>
  <div class="abs work-bg"></div>
  <div class="abs work-card"></div>
  <h2 class="abs sec-title" style="top:1460px">WORK EXPERIENCES</h2>
  <svg class="abs" style="top:1530px;left:376px" width="46" height="530" viewBox="0 0 46 530">
    <g stroke="#2746c6" stroke-width="2.5" fill="none">
      <line x1="23" y1="43" x2="23" y2="118"/><line x1="23" y1="168" x2="23" y2="289"/><line x1="23" y1="339" x2="23" y2="452"/>
      <circle cx="23" cy="29" r="19"/><circle cx="23" cy="166" r="19" transform="translate(0 -22)"/><circle cx="23" cy="334" r="19" transform="translate(0 -20)"/><circle cx="23" cy="477" r="19"/>
    </g>
    <circle cx="23" cy="29" r="13" fill="#2746c6"/>
  </svg>

  <div class="abs role" style="top:1537px">SENIOR CONSULTANT<b>2015 -2016</b></div>
  <div class="abs company" style="top:1538px">NORDVEJ ASSISTANCE</div>
  <p class="abs desc" style="top:1574px;left:455px">Nunc amet tristique volutpat adipiscing vulputate phaasellus eget enim aliquam euismod lorem ispum teoro muniote lore.</p>

  <div class="abs role" style="top:1668px">SENIOR CONSULTANT<b>2017 -2018</b></div>
  <div class="abs company" style="top:1685px">HAVBUND OFFSHORE</div>
  <p class="abs desc" style="top:1719px">Nunc amet tristique volutpat adipiscing vulputate phaasellus eget enim aliquam euismod lorem ispum teoro muniote lore.</p>

  <div class="abs role" style="top:1841px">ARCHITECTCONSULTANT<b>2018 -2019</b></div>
  <div class="abs company" style="top:1848px">LUMIO SYSTEMS APS</div>
  <p class="abs desc" style="top:1883px">Nunc amet tristique volutpat adipiscing vulputate phaasellus eget enim aliquam euismod lorem ispum teoro muniote lore.</p>

  <div class="abs role" style="top:2004px">OWNER<b>2019 -PRESENT</b></div>
  <div class="abs company" style="top:2020px">KODEVÆRK</div>
  <p class="abs desc" style="top:2055px">Nunc amet tristique volutpat adipiscing vulputate phaasellus eget enim aliquam euismod lorem ispum teoro muniote lore.</p>

  <div class="abs place" style="top:1532px"><svg width="10" height="14" viewBox="0 0 10 14"><path fill="#0a2b9c" d="M5 0a5 5 0 015 5c0 4-5 9-5 9S0 9 0 5a5 5 0 015-5zm0 3a2 2 0 100 4 2 2 0 000-4z"/></svg>FREDERIKSBERG</div>
  <div class="abs place" style="top:1676px"><svg width="10" height="14" viewBox="0 0 10 14"><path fill="#0a2b9c" d="M5 0a5 5 0 015 5c0 4-5 9-5 9S0 9 0 5a5 5 0 015-5zm0 3a2 2 0 100 4 2 2 0 000-4z"/></svg>FREDERIKSBERG</div>
  <div class="abs place" style="top:1847px"><svg width="10" height="14" viewBox="0 0 10 14"><path fill="#0a2b9c" d="M5 0a5 5 0 015 5c0 4-5 9-5 9S0 9 0 5a5 5 0 015-5zm0 3a2 2 0 100 4 2 2 0 000-4z"/></svg>FREDERIKSBERG</div>
  <div class="abs place" style="top:1999px"><svg width="10" height="14" viewBox="0 0 10 14"><path fill="#0a2b9c" d="M5 0a5 5 0 015 5c0 4-5 9-5 9S0 9 0 5a5 5 0 015-5zm0 3a2 2 0 100 4 2 2 0 000-4z"/></svg>FREDERIKSBERG</div>
</section>

<section>
  <h2 class="abs sec-title" style="top:2337px;font-size:38px">EDUCATION</h2>
  <div class="abs edu-box"></div>

  <svg class="abs" style="top:2512px;left:101px" width="46" height="40" viewBox="0 0 46 40"><g fill="none" stroke="#2746c6" stroke-width="2.2"><path d="M2 11L23 3l21 8-21 8z"/><path d="M10 15v10c0 4 26 4 26 0V15"/><path d="M40 13v14"/></g></svg>
  <div class="abs edu-t" style="top:2512px;left:164px">DIPLOMA IN SOFTWARE ENGINEERING</div>
  <div class="abs edu-s" style="top:2541px;left:166px">ØRESUND TECH UNIVERSITY<br>2002 - 2005</div>

  <svg class="abs" style="top:2512px;left:706px" width="46" height="40" viewBox="0 0 46 40"><g fill="none" stroke="#2746c6" stroke-width="2.2"><path d="M2 11L23 3l21 8-21 8z"/><path d="M10 15v10c0 4 26 4 26 0V15"/><path d="M40 13v14"/></g></svg>
  <div class="abs edu-t" style="top:2512px;left:777px">COMPUTER SCIENCE</div>
  <div class="abs edu-s" style="top:2541px;left:779px">MØLLEÅ BUSINESS COLLEGE<br>1998 - 2000</div>

  <svg class="abs" style="top:2626px;left:108px" width="40" height="40" viewBox="0 0 40 40"><g fill="none" stroke="#2746c6" stroke-width="2"><rect x="2" y="12" width="36" height="26"/><path d="M14 12V4h12v8M20 4V1"/><rect x="17" y="28" width="6" height="10"/><path d="M7 18h4M7 24h4M7 30h4M29 18h4M29 24h4M29 30h4M17 18h6"/></g></svg>
  <div class="abs edu-t" style="top:2635px;left:164px">SECONDARY SCHOOL</div>
  <div class="abs edu-s" style="top:2664px;left:166px">BIRCH HILL SECONDARY SCHOOL<br>2002 - 2005</div>

  <svg class="abs" style="top:2626px;left:710px" width="40" height="40" viewBox="0 0 40 40"><g fill="none" stroke="#2746c6" stroke-width="2"><rect x="2" y="12" width="36" height="26"/><path d="M14 12V4h12v8M20 4V1"/><rect x="17" y="28" width="6" height="10"/><path d="M7 18h4M7 24h4M7 30h4M29 18h4M29 24h4M29 30h4M17 18h6"/></g></svg>
  <div class="abs edu-t" style="top:2635px;left:777px">HIGHER SCHOOL</div>
  <div class="abs edu-s" style="top:2664px;left:779px">STONEBROOK SECONDARY SCHOOL<br>1998 - 2000</div>
</section>

<section>
  <h2 class="abs sec-title" style="top:2872px;font-size:37px">PROFESSIONAL SKILLS</h2>
  <div class="abs mont" style="top:2934px;left:0;width:1200px;text-align:center;font-size:22px;color:var(--ink)">TOP SKILLS</div>

  <svg class="abs skill-ring" style="left:154px" viewBox="0 0 186 186"><circle cx="93" cy="93" r="84" fill="none" stroke="#d6d6d6" stroke-width="18"/><circle cx="93" cy="93" r="84" fill="none" stroke="#2342c0" stroke-width="18" stroke-dasharray="517 528" transform="rotate(-86 93 93)"/><text x="93" y="103" text-anchor="middle" font-family="Montserrat,sans-serif" font-size="27" fill="#222">98%</text></svg>
  <svg class="abs skill-ring" style="left:505px" viewBox="0 0 186 186"><circle cx="93" cy="93" r="84" fill="none" stroke="#d6d6d6" stroke-width="18"/><circle cx="93" cy="93" r="84" fill="none" stroke="#2342c0" stroke-width="18" stroke-dasharray="517 528" transform="rotate(-86 93 93)"/><text x="93" y="110" text-anchor="middle" font-family="Montserrat,sans-serif" font-size="27" fill="#222">98%</text></svg>
  <svg class="abs skill-ring" style="left:866px" viewBox="0 0 186 186"><circle cx="93" cy="93" r="84" fill="none" stroke="#d6d6d6" stroke-width="18"/><circle cx="93" cy="93" r="84" fill="none" stroke="#2342c0" stroke-width="18" stroke-dasharray="517 528" transform="rotate(-86 93 93)"/><text x="93" y="110" text-anchor="middle" font-family="Montserrat,sans-serif" font-size="27" fill="#222">98%</text></svg>

  <div class="abs skill-label" style="left:74px">SOFTWARE CONTRACTOR</div>
  <div class="abs skill-label" style="left:418px">ARCHITECT</div>
  <div class="abs skill-label" style="left:779px">TECH TRAINER</div>
  <p class="abs skill-desc" style="left:88px">Lorem ipsum dolor sit amet, consectetur adipiscing elit, sed do eiusmod tempor incididunt ut labore et dolore magna aliqua. Ut enim ad</p>
  <p class="abs skill-desc" style="left:449px">Lorem ipsum dolor sit amet, consectetur adipiscing elit, sed do eiusmod tempor incididunt ut labore et dolore magna aliqua. Ut enim ad</p>
  <p class="abs skill-desc" style="left:810px">Lorem ipsum dolor sit amet, consectetur adipiscing elit, sed do eiusmod tempor incididunt ut labore et dolore magna aliqua. Ut enim ad</p>
</section>

<footer>
  <div class="abs touch"></div>
  <h2 class="abs touch-h">GET IN TOUCH</h2>
  <div class="abs touch-photo" role="img" aria-label="Round portrait photo of Daniel Hartvig"></div>
  <p class="abs touch-p">Lorem ipsum dolor sit amet, consectetur adipiscing elit, sed do eiusmod tempor incididunt ut labore et dolore magna aliqua. Ut enim ad minim veniam, quis nostrud exercitation ullamco laboris nisi ut aliquip ex ea commodo consequat. Duis aute irure dolor in reprehenderit in voluptate velit esse cillum dolore eu fugiat nulla pariatur. Excepteur sint occaecat cupidatat non proident, sunt in culpa qui officia deserunt mollit anim</p>
  <div class="abs touch-mail">Drop me a line at info@danielhartvig.com or call me at &nbsp;8888 888 8888</div>
  <div class="abs footer"></div>
  <div class="abs footer-copy">Copyright 2020 Daniel Hartvig. | All Rights Reserved</div>
  <div class="abs footer-social" aria-label="Social links">
    <span class="sq"></span><span class="sq"></span><span class="sq"></span><span class="sq"></span>
    <svg width="30" height="24" viewBox="0 0 30 24"><rect x="1.5" y="1.5" width="27" height="21" rx="2" fill="none" stroke="#fff" stroke-width="2.5"/><path d="M2 3l13 10 13-10" fill="none" stroke="#fff" stroke-width="2.5"/></svg>
  </div>
</footer>

</body>
</html>
```